Church Website with Home Page and Member Sermon Library

I am in need of an updated design for our church website. This will include 4 pages (outlined below). We are a conservative, evangelical, Christian church. The site should be modern and clean, while still reflecting our conservative values. I already have a logo for our church, and I want the site to incorporate the logo, and match the logo/branding. Stock photos are allowed if needed, but I have uploaded some images of our church and would prefer those images to be used if possible. Any stock photos used should not include any people in the photos (scenery, nature, buildings, animals, etc. are fine).

The site will need 4 pages: Home, Support Us (Donate), Login, and Recording Library.

Page 1: Home
The home page should include the following sections:

- Navigation: Should include links to each section of the home page plus a "listen live" link which will take the user to a live-streaming site and a "support us" link which will take the user to a support/donate page.

- Announcements: Can be either a banner or some other design, but there needs to be some way for us to post announcements for visitors to see. I'm open for creative ideas in this section, but would like it not to take up a lot of room on the page.

- About Us: Should include address, service times (see attached document), and information about the church.

- Pastor Bio: A section that introduces our pastor and gives a short bio about our pastor. Would like this section to include a picture of our pastor. Somewhere in this section I would like to include this Bible reference: "And I will give you pastors according to mine heart, which shall feed you with knowledge and understanding. Jer 3:15 LPW"

- Articles of Faith (What We Believe): This should include several sub-sections each with a heading, body, and possibly 1 or more scripture references. I have attached a document to the brief that includes our articles of faith. Feel free to be creative with this section in how you lay these out and format them.

- Support Us: A small section that explains what kind of support someone can give and a link to a donation page. The link can say something like "Support Us" or "Donate Now".

- Contact form: A contact form that allows the visitor to send us a message. The contact form should ask for name, email, phone, and message.

- Footer: A footer that will be displayed on all pages of the site. This should include at a minimum a link to the home page (or a link to each individual section in the home page if you prefer), a link to "listen live", a link to "support us", a link to "contact us" (or you can put the contact form directly in the footer if you prefer), the address, and a "member login" link.

Page 2: Support Us
The donation page should include a form the visitor can fill out to make a donation. We will embed a third party form later. For this design, please just mock out the design with a basic form asking for name, phone, and email.

Page 3: Login
The recording library (detailed below) will require members to login with a shared numeric code before accessing the page. We need a design for a login screen. The screen should include navigation/footer just like all other pages, but the body of the login page will consist only of a form that asks the user to enter the access code and then a "login" button.

Page 4: Recording Library

The library page is a member-only page that will require a shared, numeric pass code to access. On this page, members will be able to access a filterable list of past sermons. The page by default should display most recent sermons, but should also include a search form that allows the member to filter the sermon list to find a particular sermon. The search form should allow the user to select a filter type (e.g. Speaker name, date, event, etc.) and type in a value to search. They should be able to add multiple filters and remove filters that have been added. Each sermon that is displayed in the result list should include basic information such as title, date, speaker, tags, etc. along with a download icon, and an embedded audio player where they can click a play button to stream it on-demand. Each sermon should also have clickable tags associated with it that can be used to find related sermons.
Updates

I have uploaded several images of our church. Feel free to incorporate these into your design if possible.

Target Market(s)

Church Members

Industry/Entity Type

Religion

Number of Pages Required

4 page

Font styles to use
Sans Serif

Colors

Designer to choose colors to be used in the design.

Requirements
Must have
• Must incorporate the logo (attached)
Nice to have
• Would like the design to incorporate pictures of our church (attached) instead of stock photos if possible.
Should not have
• Please avoid an overly cluttered design. Stock photos used should not include any people in the photos.

```html
<!DOCTYPE html>
<html lang="en">
<head>
<meta charset="utf-8">
<title>Bethel Grace Church</title>
<link href="https://fonts.googleapis.com/css2?family=Cinzel:wght@400;500;600&family=Montserrat:ital,wght@0,400;0,500;0,600;1,400&display=swap" rel="stylesheet">
<style>
:root{
  --green:#7fa66a;
  --green-dark:#6b9157;
  --teal:#3fb1c8;
  --navy:#4b6a88;
  --ink:#2a2a2a;
  --text:#6a6a6a;
  --muted:#9a9a9a;
  --panel:#f1f1f1;
  --dark:#303030;
  --line:#d9d9d9;
}
*{margin:0;padding:0;box-sizing:border-box}
html,body{width:1200px;height:4704px;overflow:hidden}
body{position:relative;background:#fff;font-family:'Montserrat',sans-serif;color:var(--text)}
.abs{position:absolute}
.serif{font-family:'Cinzel',serif}
a{color:inherit;text-decoration:none}

/* hero */
.hero{position:absolute;left:0;top:0;width:1200px;height:599px;overflow:hidden}
.hero-photo{position:absolute;inset:0;background:linear-gradient(180deg,#ffffff 0%,#f6f6f6 22%,#dcdcdc 36%,#b9a697 50%,#9c7a60 64%,#8a6a52 80%,#6f6a60 92%,#8a8378 100%)}
.brand{position:absolute;left:139px;top:86px;width:162px;text-align:center;font-family:'Cinzel',serif;font-weight:400;color:var(--green);font-size:22px;letter-spacing:2px;line-height:1.1}
.brand-dot{position:absolute;left:208px;top:28px;width:24px;height:24px;border-radius:50%;background:var(--teal)}
.nav{position:absolute;top:42px;left:594px;display:flex;align-items:center;gap:30px;font-size:13px;color:var(--ink)}
.nav .login{display:flex;align-items:center;gap:5px}
.btn{display:inline-flex;align-items:center;justify-content:center;gap:8px;background:var(--green);color:#fff;font-family:'Cinzel',serif;font-size:14px;letter-spacing:.5px}
.nav .btn{width:150px;height:42px;border:2px solid #a9c59a}
.hero-title{position:absolute;top:188px;left:0;width:1200px;text-align:center;font-family:'Cinzel',serif;font-size:62px;letter-spacing:6px;color:var(--ink);font-weight:400}
.rule{position:absolute;height:3px;background:var(--navy)}
.rule.teal{background:var(--teal)}
.listen{position:absolute;left:486px;top:316px;width:226px;height:64px;border-radius:32px;background:#fff;border:3px solid #a9c59a;display:flex;align-items:center;gap:20px;padding-left:6px;font-family:'Cinzel',serif;color:var(--green);font-size:15px}
.listen .icon{width:50px;height:50px;border-radius:50%;background:var(--green);display:flex;align-items:center;justify-content:center}

/* about */
.arch-outline{position:absolute;left:110px;top:680px;width:420px;height:560px}
.arch-photo{position:absolute;left:159px;top:730px;width:318px;height:519px;border-radius:159px 159px 0 0/240px 240px 0 0;background:linear-gradient(180deg,#c9c4bd 0%,#b0866a 35%,#9b6f55 70%,#8c7560 100%)}
.eyebrow{font-size:13px;letter-spacing:1px;color:var(--teal);text-transform:uppercase}
.about-text{position:absolute;left:572px;top:741px;width:450px}
.about-text h2{font-family:'Cinzel',serif;font-weight:400;font-size:35px;line-height:41px;letter-spacing:3px;color:var(--ink);margin-top:8px}
.about-text p{font-size:12.5px;line-height:22px;margin-top:14px}
.about-text .rule-block{width:152px;height:3px;background:var(--teal);margin-top:22px}
.about-text .rule-thin{width:70px;height:1px;background:var(--teal);margin-top:-10px;margin-bottom:28px}
.about-text h3{font-family:'Cinzel',serif;font-weight:500;font-size:17px;letter-spacing:1.5px;color:var(--ink);margin-top:36px}
.times{list-style:none;margin-top:14px}
.times li{font-family:'Cinzel',serif;font-size:13px;letter-spacing:1px;color:var(--ink);line-height:33px}
.times li span{color:var(--muted);margin-right:8px}
.times li b{font-weight:600;margin-left:6px}

/* banner */
.banner{position:absolute;left:177px;top:1370px;width:840px;height:301px}
.banner-logo{position:absolute;left:537px;top:1330px;width:130px;text-align:center;font-family:'Cinzel',serif;color:var(--green);font-size:17px;line-height:20px;letter-spacing:1px}
.banner h2{position:absolute;top:90px;left:0;width:100%;text-align:center;font-family:'Cinzel',serif;font-weight:400;font-size:38px;letter-spacing:4px;color:var(--ink)}
.banner .lede{position:absolute;top:142px;left:140px;width:560px;text-align:center;font-size:13px;line-height:22px;color:var(--ink)}
.banner .meta-left{position:absolute;top:205px;left:210px;width:150px;text-align:right;font-family:'Cinzel',serif;color:var(--ink)}
.banner .meta-left .t{font-size:19px;letter-spacing:2px}
.banner .meta-left .d{font-size:11px;letter-spacing:1px;margin-top:6px;color:var(--text)}
.banner .divider{position:absolute;top:205px;left:374px;width:1px;height:58px;background:#bbb}
.banner .meta-right{position:absolute;top:208px;left:440px;color:var(--ink)}
.banner .meta-right .t{font-family:'Cinzel',serif;font-size:13px;letter-spacing:1px;line-height:15px}
.banner .meta-right .p{font-size:12px;font-style:italic;margin-top:6px}

/* pastor */
.pastor{position:absolute;left:0;top:1689px;width:1200px;height:736px;background:linear-gradient(180deg,#fbf7f7 0%,#f3ecec 40%,#efe9e9 75%,#e4dcdc 100%)}
.center-head{position:absolute;left:0;width:1200px;text-align:center}
.center-head h2{font-family:'Cinzel',serif;font-weight:400;font-size:33px;line-height:40px;letter-spacing:3px;color:var(--ink);margin-top:6px}
.pastor .col{position:absolute;top:237px;width:250px;font-size:13px;line-height:22px;color:var(--text)}
.pastor .col p+p{margin-top:16px}
.pastor .col .more{display:inline-block;margin-top:16px;font-family:'Cinzel',serif;font-size:14px;color:#9fbc8f;border-bottom:1px solid #c8d8be;padding-bottom:4px}
.portrait-ring{position:absolute;left:467px;top:203px;width:268px;height:268px;border-radius:50%;background:#fff;border:2px solid #cfcfcf;display:flex;align-items:center;justify-content:center}
.portrait{width:246px;height:246px;border-radius:50%;background:radial-gradient(circle at 50% 40%,#d9c9b4 0%,#a98d72 45%,#3d3a38 80%)}
.pastor .name{position:absolute;top:484px;left:0;width:1200px;text-align:center;color:var(--ink)}
.pastor .name small{display:block;font-size:8px;letter-spacing:1px}
.pastor .name span{font-family:'Cinzel',serif;font-size:16px;letter-spacing:1px}
.pastor blockquote{position:absolute;top:558px;left:280px;width:640px;text-align:center;font-style:italic;font-size:17px;line-height:28px;color:#555}
.pastor .ref{position:absolute;top:636px;left:0;width:1200px;text-align:center;font-family:'Cinzel',serif;font-size:17px;color:#444}

/* articles */
.article{position:absolute;width:236px}
.article h3{font-family:'Cinzel',serif;font-weight:400;font-size:17px;letter-spacing:1.5px;line-height:22px;color:var(--ink);padding-left:16px;position:relative}
.article h3::before{content:"";position:absolute;left:0;top:9px;width:5px;height:5px;border-radius:50%;background:var(--green)}
.article p{font-size:12px;line-height:20px;color:var(--text);margin-top:12px}
.article u{color:#555}
.article .end{width:210px;height:1px;background:var(--line);margin-top:26px}
.refs{list-style:none;margin-top:14px}
.refs li{font-size:10px;line-height:23.5px;color:#555}
.refs li span{font-family:'Cinzel',serif;font-size:12px;color:var(--green);margin-right:6px}
.refs li u{color:#555}

/* support + contact */
.support-photo{position:absolute;left:0;top:3323px;width:1200px;height:1381px;background:linear-gradient(180deg,#ffffff 0%,#f4f2f0 9%,#c8bdb3 18%,#9d7f69 28%,#7d624e 36%,#5a4d43 44%,#3e3a37 52%,#313030 60%,#303030 100%)}
.support-head{top:3370px}
.support-head h2{font-size:34px;line-height:46px}
.support-btn{position:absolute;left:524px;top:3510px;width:152px;height:44px;border:2px solid #a9c59a}
.contact-head{top:3896px}
.contact-head .eyebrow{color:#e0e0e0;font-family:'Cinzel',serif;font-size:17px;letter-spacing:2px}
.contact-head h2{color:#fff;font-size:34px;margin-top:0}
.field{position:absolute;background:#fff;border:2px solid #cfcfcf;font-size:11px;color:#555;padding:14px 16px}
.send{position:absolute;left:533px;top:4247px;width:141px;height:48px;border:2px solid #a9c59a}

/* footer */
.foot-head{font-family:'Cinzel',serif;font-size:16px;letter-spacing:1.5px;color:#e8e8e8}
.foot-donate{position:absolute;left:152px;top:4436px;width:280px;text-align:center}
.foot-donate p{font-size:12px;line-height:19px;color:#cfcfcf;margin-top:14px}
.foot-donate .btn{width:152px;height:42px;margin-top:26px;border:2px solid #a9c59a}
.foot-brand{position:absolute;left:470px;top:4510px;width:260px;text-align:center;font-family:'Cinzel',serif;color:var(--green);font-size:34px;letter-spacing:3px;line-height:40px}
.foot-links{position:absolute;left:822px;top:4436px}
.foot-links ul{list-style:none;margin-top:16px}
.foot-links li{font-size:13px;color:#d6d6d6;line-height:32px}
.copyright{position:absolute;left:86px;top:4667px;font-size:11px;color:#d0d0d0}
.social{position:absolute;left:935px;top:4666px;display:flex;gap:15px}
.social span{width:11px;height:11px;border-radius:50%;background:#e6e6e6;display:block}
</style>
</head>
<body>

<!-- hero -->
<header class="hero">
  <div class="hero-photo" role="img" aria-label="Photo of the brick church building with its sign, under a pale sky"></div>
  <div class="brand-dot"></div>
  <div class="brand">Bethel<br>Grace</div>
  <nav class="nav">
    <a href="#">Home</a>
    <a href="#">Recording Library</a>
    <a href="#" class="login">
      <svg width="12" height="13" viewBox="0 0 12 13" fill="none" stroke="#2a2a2a" stroke-width="1.3"><circle cx="6" cy="4" r="3"/><path d="M1 12.5c0-3 2.2-4.8 5-4.8s5 1.8 5 4.8"/></svg>Login
    </a>
    <a href="#" class="btn">Support Us</a>
  </nav>
  <h1 class="hero-title">Keep Faith Always</h1>
  <div class="rule" style="left:519px;top:277px;width:162px"></div>
  <a href="#" class="listen">
    <span class="icon">
      <svg width="28" height="28" viewBox="0 0 28 28" fill="none" stroke="#fff" stroke-width="1.6"><circle cx="14" cy="12" r="2.5" fill="#fff"/><path d="M9.5 7.5a6.5 6.5 0 0 0 0 9M18.5 7.5a6.5 6.5 0 0 1 0 9M6.5 4.5a10.5 10.5 0 0 0 0 15M21.5 4.5a10.5 10.5 0 0 1 0 15"/></svg>
    </span>
    Listen Live
  </a>
</header>

<!-- about -->
<section class="about">
  <svg class="arch-outline" viewBox="0 0 420 560" fill="none" stroke="#ececec" stroke-width="6"><path d="M10 560V270C10 130 110 40 210 5C310 40 410 130 410 270V560"/></svg>
  <div class="arch-photo" role="img" aria-label="Photo of the church entrance with its marquee sign, framed as an arch"></div>
  <div class="about-text">
    <div class="eyebrow">About</div>
    <h2>Welcome to<br>Bethel Grace<br>Church</h2>
    <p>Ut diam tortor consectetur lacus scelerisque tortor congue viverra egestas. Tristique in consectetur leo arcu blandit diam et sed volutpat.</p>
    <p>Aliquam at commodo venenatis quis. Velit neque interdum molestie risus consectetur vestibulum a eget. Ultricies volutpat orci eros quisque ullamcorper quis est.</p>
    <div class="rule-block"></div>
    <h3>Service Time Are</h3>
    <ul class="times">
      <li><span>01.</span>Wednesday Evening Service: <b>7:30 PM</b></li>
      <li><span>02.</span>Sunday School: <b>10:00 AM</b></li>
      <li><span>03.</span>Sunday Morning Service: <b>11:00 AM</b></li>
      <li><span>04.</span>Sunday Evening Service: <b>5:30 PM</b></li>
    </ul>
  </div>
</section>

<!-- announcement -->
<section class="banner">
  <svg width="840" height="301" viewBox="0 0 840 301" style="position:absolute;left:0;top:0" fill="none">
    <path d="M30 3H360A65 65 0 0 0 490 3H810A30 30 0 0 0 837 30V271A30 30 0 0 0 810 298H30A30 30 0 0 0 3 271V30A30 30 0 0 0 30 3Z" stroke="#4b6a88" stroke-width="6" fill="#f1f1f1"/>
    <path d="M40 14H352A73 73 0 0 0 498 14H800A30 30 0 0 0 826 40V261A30 30 0 0 0 800 287H40A30 30 0 0 0 14 261V40A30 30 0 0 0 40 14Z" stroke="#4b6a88" stroke-width="1.5"/>
  </svg>
  <h2>Announcement Banner Spot</h2>
  <p class="lede">Ullamcorper facilisi egestas semper fames suscipit penatibus amet. Ut diam tortor consectetur lacus scelerisque tortor congue viverra</p>
  <div class="meta-left"><div class="t">Announcement</div><div class="d">Fabruary 16th</div></div>
  <div class="divider"></div>
  <div class="meta-right"><div class="t">Bethel Grace<br>Church</div><div class="p">Pastor John Doe</div></div>
</section>
<div class="banner-logo">Bethel<br>Grace</div>

<!-- pastor -->
<section class="pastor" role="img" aria-label="Soft blurred photo of the church sanctuary as section background">
  <div class="center-head" style="top:65px">
    <div class="eyebrow">Our Pastor</div>
    <h2>A Man of Prayer and High<br>Spirituality</h2>
  </div>
  <div class="col" style="left:172px">
    <p>Ullamcorper facilisi egestas semper fames suscipit penatibus amet. Ut diam tortor consectetur lacus scelerisque tortor congue viverra egestas. Tristique in consectetur leo arcu blandit diam et sed volutpat.</p>
    <p>Aliquam at commodo venenatis quis. Velit neque interdum molestie risus consectetur vestibulum a eget.</p>
  </div>
  <div class="portrait-ring"><div class="portrait" role="img" aria-label="Portrait photo of the pastor"></div></div>
  <div class="col" style="left:767px">
    <p>Ut diam tortor consectetur lacus scelerisque tortor congue viverra egestas. Tristique in consectetur leo arcu blandit diam et sed volutpat.</p>
    <p>Aliquam at commodo venenatis quis. Velit neque interdum molestie risus consectetur vestibulum a eget.</p>
    <a href="#" class="more">Read Full Bio</a>
  </div>
  <div class="name"><small>PASTOR</small><span>John Doe</span></div>
  <div class="rule teal" style="left:517px;top:533px;width:164px"></div>
  <blockquote>"And I will give you pastors according to mine heart, which shall feed you with knowledge and understanding."</blockquote>
  <div class="ref">Jer 3:15 LPW</div>
</section>

<!-- articles of faith -->
<section class="articles">
  <div class="center-head" style="top:2538px"><h2 style="margin:0">Articles of Faith</h2></div>
  <div class="rule teal" style="left:519px;top:2594px;width:162px"></div>

  <div class="article" style="left:168px;top:2645px">
    <h3>The God Head.</h3>
    <p>We believe in the God head bodily, known as the Divine Trinity. This body consist of God the father, Jesus Christ, his only begotten son and the redeemer of the world, and of the Holy Ghost, The third person of the Divine Trinity</p>
    <div class="end"></div>
  </div>
  <div class="article" style="left:168px;top:2912px">
    <h3>Baptism of the Holy Ghost.</h3>
    <p>We believe in the baptism of the Holy Ghost as it is taught in the Bible and promised by our Lord Jesus Christ, with speaking in tongues as the Spirit gives utterance as the initial evidence. <u>Acts 2:4</u> we believe that the gift of the Holy Ghost is for all believers as the Lord promised. <u>Acts 2:17-18</u></p>
    <div class="end"></div>
  </div>

  <div class="article" style="left:464px;top:2645px">
    <h3>Full Salvation.</h3>
    <p>We believe that Salvation is received only when a person comes to the realization that he or she is lost and separated from God and becomes full of godly sorrow, confessing their sins and true repentance, believing in the shed blood of the Lord Jesus Christ as the only sacrifice for sins. Through the blood of Christ we have:</p>
    <ul class="refs">
      <li><span>01.</span><u>Remission of sins, Matthew 26:28 Heb 9:22</u></li>
      <li><span>02.</span><u>Sanctification, Hebrews 13:12</u></li>
      <li><span>03.</span><u>Redemption, Revelations 5:9</u></li>
      <li><span>04.</span><u>Cleansing, 1 John 1:7 Rev. 1:5</u></li>
      <li><span>05.</span><u>Justification, Romans 5:9</u></li>
    </ul>
    <div class="end" style="margin-top:20px"></div>
  </div>
  <div class="article" style="left:464px;top:3069px">
    <h3>Second Coming of Christ.</h3>
    <p>We believe in the second coming of Jesus Christ. <u>Matthew 24:44</u> <u>Luke 12:40</u></p>
  </div>

  <div class="article" style="left:772px;top:2645px">
    <h3>Sanctification</h3>
    <p>"Sanctify them through thy truth thy word is truth <u>St John 17:17</u>. For this is the will of God even your sanctification"</p>
    <p>We believe in a set apart life, separate from the world to Christ <u>2 Cor 6:17-18</u></p>
    <div class="end"></div>
  </div>
  <div class="article" style="left:772px;top:2899px">
    <h3>Divine Healing.</h3>
    <p>We believe Divine Healing to be included in the atonement of Jesus Christ our Lord, And believe that it is still for us today. <u>1 Peter 2:24</u> <u>Luke 9:1-2</u> <u>Mark 16:18</u> <u>James 5:15</u></p>
    <div class="end"></div>
  </div>
  <div class="article" style="left:772px;top:3110px">
    <h3>Eternity</h3>
    <p>We believe in Literal Eternity. Eternal Life for the believer and eternal death for those without Christ. <u>Revelations 21:1-27</u></p>
  </div>
</section>

<!-- support & contact -->
<div class="support-photo" role="img" aria-label="Photo of the church building fading into a dark background"></div>
<section class="center-head support-head">
  <div class="eyebrow">Support Us</div>
  <h2>Where Your Treasure Is, Your<br>Heart Is As Well</h2>
</section>
<a href="#" class="btn support-btn">Support Us</a>

<section class="center-head contact-head">
  <div class="eyebrow">Contact Us</div>
  <h2>Feel Free to Join Us</h2>
</section>
<div class="field" style="left:166px;top:3993px;width:426px;height:44px">Name *</div>
<div class="field" style="left:614px;top:3993px;width:421px;height:44px">Phone *</div>
<div class="field" style="left:166px;top:4054px;width:869px;height:44px">Email address *</div>
<div class="field" style="left:166px;top:4112px;width:869px;height:110px">Message</div>
<a href="#" class="btn send">Send Us
  <svg width="20" height="10" viewBox="0 0 20 10" fill="none" stroke="#fff" stroke-width="1.5"><path d="M0 5h18M14 1l4 4-4 4"/></svg>
</a>

<!-- footer -->
<footer>
  <div class="foot-donate">
    <div class="foot-head">Donation</div>
    <p>Aliquam at commodo venenatis quis. Velit neque interdum molestie risus.</p>
    <a href="#" class="btn">Support Us</a>
  </div>
  <div class="foot-brand">Bethel<br>Grace</div>
  <div class="foot-links">
    <div class="foot-head">Quick Links</div>
    <ul>
      <li><a href="#">Home</a></li>
      <li><a href="#">Recording Library</a></li>
      <li><a href="#">Contact Us</a></li>
      <li><a href="#">Login</a></li>
    </ul>
  </div>
  <div class="copyright">Copyright 2023 Bethel Grace Church I All rights reserved</div>
  <div class="social">
    <span aria-label="Social link"></span>
    <span aria-label="Social link"></span>
    <span aria-label="Social link"></span>
    <span aria-label="Social link"></span>
  </div>
</footer>

</body>
</html>
```